Money Mindset Podcast needs fun, creative cover art

Launching a new podcast called 'Turning Your Thoughts Toward Savings' - aimed at an audience 30-50 who are interested in the practicalities of managing their money but also the more mental and emotional aspects.
Looking for something not too serious, warm and friendly.

Must be easy to read on phone screens
3000 x 3000 in size
Avoid currency symbols $, £ etc, as may have an international audience

Target Market(s)

Podcast listeners age 30-50 starting in the UK but then worldwide. Probably 60:40 female bias

Industry/Entity Type

Life Coaching

Font styles to use
Serif
Sans Serif

Colors
cadf82
fee18a
acd037
85cae6
eea4c8
f59195
85acd3

Requirements
Must have
• Simple, clear design. Easy to read on variety of devices. 3000 x 3000
Appeal to those with a spiritual or emotional interests
Nice to have
• Stand out among other money related podcasts
Maybe play around with clouds, lightbulbs and clearing skies
Should not have
• Currency symbols such as $ or £
Be too corporate or bank like
Stock images

```html
<!DOCTYPE html>
<html lang="en">
<head>
<meta charset="utf-8">
<title>Turning Your Thoughts Toward Savings — Podcast Cover</title>
<link href="https://fonts.googleapis.com/css2?family=Delius&display=swap" rel="stylesheet">
<style>
  :root {
    --sky-pale: #e6fbff;
    --sky-light: #a9ecf7;
    --sky-mid: #6fd3ef;
    --sky-deep: #4bb8e6;
    --bulb-glow: #f2ffff;
    --bulb-cyan: #5fe3ea;
    --bulb-teal: #2fc7d3;
    --socket-grey: #5f7273;
    --ink-navy: #0f3f5f;
    --accent-pink: #e8168c;
  }
  html, body {
    margin: 0;
    padding: 0;
    width: 1200px;
    height: 1200px;
    overflow: hidden;
    background: var(--sky-light);
  }
  .cover {
    position: relative;
    width: 1200px;
    height: 1200px;
    overflow: hidden;
    font-family: "Delius", "Comic Sans MS", sans-serif;
    background:
      radial-gradient(circle at 50% 52%, var(--sky-pale) 0%, var(--sky-light) 38%, var(--sky-mid) 72%, var(--sky-deep) 100%);
  }
  .bulb-illustration {
    position: absolute;
    left: 190px;
    top: 150px;
    width: 820px;
    height: 1080px;
    border-radius: 50% 50% 28% 28% / 42% 42% 30% 30%;
    background:
      radial-gradient(ellipse at 50% 36%, var(--bulb-glow) 0%, var(--bulb-cyan) 45%, var(--bulb-teal) 78%, var(--socket-grey) 100%);
    opacity: 0.85;
  }
  .title {
    position: absolute;
    inset: 0;
    margin: 0;
    font-weight: 400;
    transform: rotate(-6deg);
    transform-origin: 50% 45%;
  }
  .title span {
    position: absolute;
    display: block;
    white-space: nowrap;
    line-height: 1;
  }
  .title-lead {
    left: 150px;
    top: 235px;
    font-size: 104px;
    color: var(--ink-navy);
  }
  .title-key {
    left: 150px;
    top: 355px;
    font-size: 182px;
    color: var(--accent-pink);
  }
  .title-link {
    left: 1000px;
    top: 250px;
    font-size: 74px;
    color: var(--accent-pink);
    transform: rotate(90deg);
    transform-origin: 0 0;
  }
  .title-end {
    left: 130px;
    top: 560px;
    font-size: 236px;
    color: var(--ink-navy);
  }
</style>
</head>
<body>
  <main class="cover">
    <div class="bulb-illustration" role="img" aria-label="Glowing cyan lightbulb illustration with a grey screw base, on a background of soft concentric blue rings"></div>
    <h1 class="title">
      <span class="title-lead">turning your</span>
      <span class="title-key">thoughts</span>
      <span class="title-link">toward</span>
      <span class="title-end">savings</span>
    </h1>
  </main>
</body>
</html>
```